Design a website for our small self storage business

We're looking for a freelance web designer who can produce a good-looking design for our small business website (no coding necessary). We will provide a list of pages to design, along with content outlines.

Key skills:
- Graphic design
- Responsive web design
- Proficiency with a modern web design tool such as Figma, Adobe Xd, or InVision

Please send relevant previous work (preferably in an inspectable format such as Figma or Invision).

```html
<!DOCTYPE html>
<html lang="en">
<head>
<meta charset="utf-8">
<title>Maple Crest Self Storage</title>
<link href="https://fonts.googleapis.com/css2?family=Montserrat:wght@500;600;700&family=Roboto:wght@400;500;700&display=swap" rel="stylesheet">
<style>
:root{
  --red:#e3212b;
  --blue:#0b4a8b;
  --navy:#0a3d75;
  --ink:#1d1d1f;
  --text:#555a61;
  --pale:#eef5fd;
  --line:#dfe4ea;
  --footer:#1e1e1e;
}
*{box-sizing:border-box;margin:0;padding:0}
html,body{width:1200px;height:3677px;overflow:hidden}
body{position:relative;background:#fff;font-family:"Roboto",sans-serif;color:var(--text)}
.abs{position:absolute}
.btn{position:absolute;display:flex;align-items:center;justify-content:center;gap:8px;border-radius:26px;color:#fff;font-weight:700;font-size:15px;text-transform:uppercase;font-family:"Roboto",sans-serif}
.btn .arrow{width:15px;height:15px;border-radius:50%;background:#fff;position:relative}
.btn .arrow::after{content:"";position:absolute;left:4px;top:4px;border:4px solid transparent;border-left:6px solid var(--red);border-right:none;}
.btn.red{background:var(--red)}
.btn.blue{background:var(--blue)}
.btn.blue .arrow::after{border-left-color:var(--blue)}

/* header */
.topline{left:0;top:0;width:1200px;height:4px;background:var(--navy)}
.brand{left:112px;top:20px;display:flex;align-items:center;gap:8px}
.brand .mark{width:18px;height:18px;background:var(--red)}
.brand .name{font-weight:700;font-size:20px;color:var(--blue);line-height:1.05;width:110px}
.nav{left:374px;top:34px;display:flex;gap:30px;font-size:15px;font-weight:500;color:var(--ink)}
.nav .active{color:var(--red)}
.quote{left:735px;top:26px;width:142px;height:38px;font-size:15px;text-transform:none}
.callicon{left:906px;top:27px;width:36px;height:36px;border-radius:50%;background:var(--blue)}
.call{left:955px;top:24px;font-size:12px;color:var(--text)}
.call b{display:block;font-size:19px;color:var(--ink);margin-top:2px}

/* hero */
.hero{left:0;top:88px;width:1200px;height:730px;background:linear-gradient(180deg,#5a86b8 0%,#7a5f72 35%,#b3283b 55%,#8e1f2c 72%,#6e6e6e 85%,#555 100%)}
.hero-title{left:0;top:276px;width:1200px;text-align:center;font-family:"Montserrat",sans-serif;font-weight:700;font-size:37px;color:#fff}
.hero-sub{left:290px;top:340px;width:620px;text-align:center;font-size:16px;line-height:27px;color:#fff;font-weight:500}
.hero-btn{left:501px;top:416px;width:198px;height:48px;font-size:16px}
.slide-arrow{top:343px;width:42px;height:42px;border-radius:50%;background:rgba(30,30,30,.6)}
.slide-arrow svg{position:absolute;left:12px;top:11px}

/* section heading */
.heading{left:0;width:1200px;text-align:center;font-family:"Montserrat",sans-serif;font-size:33px;font-weight:500;color:var(--red)}
.heading b{color:var(--blue);font-weight:700}
.divider{display:flex;align-items:center;gap:8px;justify-content:center;width:150px}
.divider span{width:48px;height:2px;background:var(--blue)}
.divider i{width:22px;height:12px;background:var(--red);border-right:10px solid var(--blue)}

/* advantages */
.dots{background:#e6eef8}
.card-hi{left:432px;top:907px;width:336px;height:367px;background:#fff;border-radius:22px;box-shadow:0 6px 30px rgba(0,0,0,.1);border-bottom:4px solid var(--red)}
.adv{top:929px;width:300px;text-align:center}
.adv .icon{width:116px;height:116px;border-radius:50%;margin:0 auto;display:flex;align-items:center;justify-content:center}
.adv h3{font-size:19px;font-weight:500;color:var(--ink);margin-top:28px}
.adv p{font-size:14px;line-height:24px;margin-top:12px}
.adv .more{margin-top:18px;font-size:14px;font-weight:700;color:var(--red);display:flex;justify-content:center;align-items:center;gap:6px}
.adv .more i{width:13px;height:13px;border-radius:50%;background:var(--red)}

/* split */
.split-text{top:1440px;width:420px;text-align:center;color:#fff}
.split-text .circle{width:84px;height:84px;border-radius:50%;background:#fff;margin:0 auto}
.split-text h3{font-size:21px;font-weight:700;margin-top:22px}
.split-text p{font-size:14px;line-height:25px;margin-top:12px}

/* bring */
.ring{left:111px;top:1875px;width:446px;height:446px;border-radius:50%;background:#d6d6d6;padding:16px}
.ring div{width:100%;height:100%;border-radius:50%;background:radial-gradient(circle at 50% 50%,#e8edf3 0%,#9fb3c9 30%,#2d4f7e 65%,#1c3458 100%)}
.bring-h{left:630px;top:1900px;font-family:"Montserrat",sans-serif;font-size:32px;line-height:44px;font-weight:500;color:var(--red)}
.bring-h b{color:var(--blue);font-weight:700}
.bring-p{left:630px;width:460px;font-size:14px;line-height:26px}

/* contact */
.contact-bg{left:0;top:2397px;width:1200px;height:800px;background:var(--pale)}
.info{top:2548px;display:flex;gap:14px;align-items:center}
.info h4{font-size:15px;font-weight:700;color:var(--ink)}
.info p{font-size:14px;margin-top:3px}
.git{left:113px;top:2648px;font-size:23px;font-weight:700;color:var(--ink)}
.git-line{left:113px;top:2680px;width:60px;height:3px;background:var(--blue)}
.git-sub{left:113px;top:2693px;font-size:15px}
.field{position:absolute;background:#fff;border:1px solid var(--line);font-size:11px;color:#555;padding:0 20px;display:flex;align-items:center}
.submit{left:113px;top:3054px;width:460px;height:42px;font-size:16px}
.map{left:636px;top:2650px;width:451px;height:447px;background:#eef0f2;border:8px solid #fff;box-shadow:0 4px 18px rgba(0,0,0,.1)}

/* footer */
.foot-brand{left:112px;top:3420px;width:216px;text-align:center;color:#fff;font-weight:700;font-size:34px;line-height:1.05}
.foot-brand .mark{width:30px;height:30px;background:#fff;margin:0 auto 14px}
.socials{left:142px;top:3540px;display:flex;gap:9px}
.socials span{width:31px;height:31px;border-radius:50%;border:1.5px solid #fff}
.fcol{top:3373px;color:#fff}
.fcol h4{font-size:16px;font-weight:700;margin-bottom:24px}
.fcol li{list-style:none;font-size:13px;line-height:26px}
.fc-label{font-size:11px;color:var(--red);font-weight:500}
.fc-val{font-size:13px;color:#fff;line-height:18px;margin:4px 0 14px}
.cards{left:112px;top:3630px;display:flex;gap:4px}
.cards span{width:32px;height:20px;background:#e9e9e9;border-radius:2px}
.copy{left:0;width:1200px;top:3632px;text-align:center;font-size:14px;color:#ddd}
.totop{left:1107px;top:3588px;width:34px;height:34px;border-radius:50%;background:var(--blue)}
</style>
</head>
<body>

<!-- header -->
<div class="abs topline"></div>
<div class="abs brand"><span class="mark"></span><span class="name">MAPLE CREST</span></div>
<nav class="abs nav"><span class="active">Home</span><span>Units</span><span>Pay Online</span><span>Contact Us</span></nav>
<div class="btn red quote">Get A Quote</div>
<div class="abs callicon">
  <svg width="36" height="36" viewBox="0 0 36 36"><path d="M13 10c1-1 2-1 3 0l2 3c.5 1 0 2-1 2.5 .7 2 2 3.5 4 4.5.5-1 1.5-1.5 2.5-1l3 2c1 1 1 2 0 3-3 3-8 0-11-3s-5-8-2.5-11z" fill="#fff"/></svg>
</div>
<div class="abs call">Call Us Today!<b>(555) 014-2280</b></div>

<!-- hero -->
<div class="abs hero" role="img" aria-label="Row of red roll-up storage unit doors on a gravel lot under blue sky"></div>
<div class="abs slide-arrow" style="left:35px"><svg width="18" height="20"><path d="M12 2 4 10l8 8" stroke="#fff" stroke-width="2" fill="none"/></svg></div>
<div class="abs slide-arrow" style="left:1125px"><svg width="18" height="20"><path d="M6 2l8 8-8 8" stroke="#fff" stroke-width="2" fill="none"/></svg></div>
<h1 class="abs hero-title">MAPLE CREST SELF STORAGE</h1>
<p class="abs hero-sub">Maple Crest Self Storage Located on Maple Crest Rd. between Alder Ave. and Birch Ave. near Riverside Civic Center in Pine Valley.</p>
<div class="btn red hero-btn">Get Started <span class="arrow"></span></div>
<svg class="abs" style="left:0;top:600px" width="1200" height="220" viewBox="0 600 1200 220">
  <polygon points="0,790 321,643 325,656 0,805" fill="var(--red)"/>
  <polygon points="321,643 1200,735 1200,790 321,662" fill="var(--navy)"/>
  <polygon points="0,805 321,662 1200,790 1200,820 0,820" fill="#fff"/>
</svg>

<!-- key advantages -->
<h2 class="abs heading" style="top:792px">KEY <b>ADVANTAGES</b></h2>
<div class="abs divider" style="left:525px;top:840px"><span></span><i></i><span></span></div>

<div class="abs dots" style="left:412px;top:888px;width:124px;height:12px;opacity:.8"></div>
<div class="abs dots" style="left:412px;top:888px;width:12px;height:122px;opacity:.8"></div>
<div class="abs dots" style="left:774px;top:1172px;width:12px;height:124px;opacity:.8"></div>
<div class="abs dots" style="left:664px;top:1284px;width:122px;height:12px;opacity:.8"></div>

<div class="abs card-hi"></div>

<div class="abs adv" style="left:103px">
  <div class="icon" style="background:var(--navy)">
    <svg width="60" height="60" viewBox="0 0 60 60"><circle cx="32" cy="26" r="14" fill="none" stroke="#fff" stroke-width="3"/><text x="32" y="33" text-anchor="middle" font-size="20" font-weight="700" fill="#fff" font-family="Roboto,sans-serif">$</text><path d="M6 44h12l10 4h14l10-8" fill="none" stroke="#fff" stroke-width="3"/></svg>
  </div>
  <h3>Affordable</h3>
  <p>Lorem ipsum dolor sit amet, consectetur adipiscing elit, sed do eiusmod tempor incididunt ut labore et dolore magna aliqua. Ut enim ad minim veniam,</p>
  <div class="more">READ MORE <i></i></div>
</div>
<div class="abs adv" style="left:450px">
  <div class="icon" style="background:var(--red)">
    <svg width="60" height="60" viewBox="0 0 60 60"><path d="M30 6l20 7v14c0 13-9 22-20 26C19 49 10 40 10 27V13z" fill="none" stroke="#fff" stroke-width="3"/><rect x="21" y="27" width="18" height="14" rx="2" fill="#fff"/><path d="M24 27v-4a6 6 0 0 1 12 0v4" fill="none" stroke="#fff" stroke-width="3"/></svg>
  </div>
  <h3>Secure</h3>
  <p>Lorem ipsum dolor sit amet, consectetur adipiscing elit, sed do eiusmod tempor incididunt ut labore et dolore magna aliqua. Ut enim ad minim veniam,</p>
  <div class="more">READ MORE <i></i></div>
</div>
<div class="abs adv" style="left:797px">
  <div class="icon" style="background:var(--navy)">
    <svg width="60" height="60" viewBox="0 0 60 60"><circle cx="34" cy="22" r="11" fill="none" stroke="#fff" stroke-width="3"/><path d="M8 44h14l8 4h12l12-12" fill="none" stroke="#fff" stroke-width="3"/></svg>
  </div>
  <h3>Convenient</h3>
  <p>Lorem ipsum dolor sit amet, consectetur adipiscing elit, sed do eiusmod tempor incididunt ut labore et dolore magna aliqua. Ut enim ad minim veniam,</p>
  <div class="more">READ MORE <i></i></div>
</div>

<!-- split features -->
<svg class="abs" style="left:0;top:1341px" width="1200" height="500" viewBox="0 0 1200 500">
  <polygon points="0,0 600,83 600,417 0,500" fill="var(--blue)" role="img" aria-label="Blue-tinted drive-up storage units"/>
  <polygon points="600,83 1200,0 1200,500 600,417" fill="var(--red)" role="img" aria-label="Red-tinted storage shelves with boxes"/>
</svg>
<div class="abs split-text" style="left:107px">
  <div class="circle"></div>
  <h3>DRIVE-UP SPACES</h3>
  <p>Sed ut perspiciatis unde omnis iste natus error sit voluptatem accusantium doloremque laudantium, totam aperiam, eaque ipsa quae ab illo inventore veritatis et quasi architecto ipsam voluptatem beatae vitae dicta sunt explicabo.</p>
</div>
<div class="btn red" style="left:235px;top:1701px;width:164px;height:42px">Learn More <span class="arrow"></span></div>
<div class="abs split-text" style="left:707px">
  <div class="circle"></div>
  <h3>JUST SHOW UP WITH YOUR STUFF</h3>
  <p>Sed ut perspiciatis unde omnis iste natus error sit voluptatem accusantium doloremque laudantium, totam aperiam, eaque ipsa quae ab illo inventore veritatis et quasi architecto ipsam voluptatem beatae vitae dicta sunt explicabo.</p>
</div>
<div class="btn blue" style="left:835px;top:1701px;width:164px;height:42px">Learn More <span class="arrow"></span></div>

<!-- what to bring -->
<div class="abs ring"><div role="img" aria-label="Indoor storage corridor lined with blue roll-up doors"></div></div>
<h2 class="abs bring-h">WHAT SHOULD I BRING TO<br><b>RENT A SPACE?</b></h2>
<div class="abs divider" style="left:630px;top:2000px"><span></span><i></i><span></span></div>
<p class="abs bring-p" style="top:2042px">Lorem ipsum dolor sit amet, consectetur adipiscing elit, sed do eiusmod tempor incididunt ut labore et dolore magna aliqua. Ut enim ad minim veniam, quis nostrud exercitation ullamco laboris nisi ut aliquip ex ea commodo consequat.</p>
<p class="abs bring-p" style="top:2155px">Duis aute irure dolor in reprehenderit in voluptate velit esse cillum dolore eu fugiat magni dolores eos nulla pariatur.</p>
<div class="btn red" style="left:630px;top:2236px;width:170px;height:48px">Learn More <span class="arrow"></span></div>

<!-- contact -->
<div class="abs contact-bg"></div>
<h2 class="abs heading" style="top:2452px">CONTACT <b>US</b></h2>
<div class="abs divider" style="left:525px;top:2500px"><span></span><i></i><span></span></div>

<div class="abs info" style="left:113px">
  <svg width="48" height="48" viewBox="0 0 48 48"><path d="M12 8c2-2 4-2 5 0l4 6c1 2 0 3-2 4 2 5 5 8 10 10 1-2 2-3 4-2l6 4c2 1 2 3 0 5-5 5-14 1-20-5S7 13 12 8z" fill="none" stroke="var(--red)" stroke-width="2.5"/></svg>
  <div><h4>PHONE:</h4><p>(555) 014-2280</p></div>
</div>
<div class="abs info" style="left:335px">
  <svg width="48" height="48" viewBox="0 0 48 48"><rect x="6" y="16" width="36" height="26" rx="3" fill="none" stroke="var(--red)" stroke-width="2.5"/><rect x="14" y="6" width="20" height="10" fill="none" stroke="var(--red)" stroke-width="2.5"/><path d="M16 24h4M24 24h4M32 24h2M16 30h4M24 30h4M32 30h2" stroke="var(--red)" stroke-width="2.5"/></svg>
  <div><h4>FAX:</h4><p>(555) 014-2281</p></div>
</div>
<div class="abs info" style="left:563px">
  <svg width="50" height="50" viewBox="0 0 50 50"><circle cx="25" cy="25" r="20" fill="none" stroke="var(--red)" stroke-width="2.5"/><path d="M25 13v12l7 5" fill="none" stroke="var(--red)" stroke-width="2.5"/></svg>
  <div><h4>OPENING TIMES:</h4><p>Mon - Sun: 08Am to 7 Pm</p></div>
</div>
<div class="abs info" style="left:848px">
  <svg width="52" height="48" viewBox="0 0 52 48"><rect x="3" y="8" width="46" height="32" fill="none" stroke="var(--red)" stroke-width="2.5"/><path d="M3 8l23 18L49 8M3 40l17-15M49 40 32 25" fill="none" stroke="var(--red)" stroke-width="2.5"/></svg>
  <div><h4>EMAIL:</h4><p>info@maplecreststorage.example</p></div>
</div>

<h3 class="abs git">GET IN TOUCH</h3>
<div class="abs git-line"></div>
<p class="abs git-sub">Reach out to us for any inquiry</p>
<div class="field" style="left:113px;top:2742px;width:224px;height:43px">Name*</div>
<div class="field" style="left:349px;top:2742px;width:224px;height:43px">Email*</div>
<div class="field" style="left:113px;top:2804px;width:224px;height:43px">Confirm Email*</div>
<div class="field" style="left:349px;top:2804px;width:224px;height:43px">Unit Number</div>
<div class="field" style="left:113px;top:2866px;width:460px;height:43px;justify-content:space-between">Reason for contact*
  <svg width="10" height="6"><path d="M0 0h10L5 6z" fill="#333"/></svg></div>
<div class="field" style="left:113px;top:2929px;width:460px;height:90px;align-items:flex-start;padding-top:14px">Message</div>
<div class="btn red submit">Submit</div>
<div class="abs map" role="img" aria-label="Street map showing the facility location"></div>

<!-- footer -->
<svg class="abs" style="left:0;top:3140px" width="1200" height="537" viewBox="0 3140 1200 537">
  <polygon points="0,3210 885,3325 1200,3170 1200,3677 0,3677" fill="var(--footer)"/>
  <polygon points="0,3150 885,3290 885,3310 0,3195" fill="var(--navy)"/>
  <polygon points="885,3290 1200,3152 1200,3172 885,3325" fill="var(--red)"/>
  <polygon points="0,3195 885,3310 885,3325 0,3210" fill="#fff"/>
</svg>
<div class="abs foot-brand"><div class="mark"></div>MAPLE CREST</div>
<div class="abs socials"><span></span><span></span><span></span><span></span></div>

<div class="abs fcol" style="left:418px">
  <h4>Quick Links</h4>
  <ul><li>Home</li><li>Units</li><li>Pay Online</li><li>Testimonials</li><li>Contact Us</li></ul>
</div>
<div class="abs fcol" style="left:614px">
  <h4>About Company</h4>
  <ul><li>Legal Information</li><li>Terms &amp; Condition</li><li>Privacy Policy</li><li>Support</li><li>Site Map</li><li>FAQ</li></ul>
</div>
<div class="abs fcol" style="left:853px">
  <h4>Contact Us</h4>
  <div class="fc-label">● Phone</div><div class="fc-val" style="margin-left:23px">(555) 014-2282</div>
  <div class="fc-label">■ Email</div><div class="fc-val" style="margin-left:23px">hello@maplecreststorage.example</div>
  <div class="fc-label">● Location</div><div class="fc-val" style="margin-left:23px;width:210px">2140 Maple Crest Road, Pine Valley, CA 90000</div>
</div>
<div class="abs totop"><svg width="34" height="34"><path d="M11 20l6-6 6 6" stroke="#fff" stroke-width="2" fill="none"/></svg></div>
<div class="abs cards"><span></span><span></span><span></span><span></span><span></span></div>
<p class="abs copy">© 2022 Maple Crest Self Storage &nbsp;|&nbsp; All Rights Reserved</p>

</body>
</html>
```